Vindgerdi - Start-up company selling electricity

Hello let me tell you about Vindgerdi.

Vindgerdi is start-up company selling electricity in Iceland. The operations of the company consist of making power usage forecasts for our customers, purchasing the electricity wholesale from the energy producers, and selling the electricity to the consumer. We are focused on tech by using optimization and machine learning to minimize electricity prices to our customers. Our marketing strategy is to portray a tech company mindset and to show dedication to driving down the electricity price on the market.

We need your help to make our website pop. Possible concepts to work with are as follows:

- Iceland the land of ice and fire
- Green energy
- Innovation
- Tech and data science

Link to our website: https://prufa.vindgerdi-example.is/
We are open to ideas.
Thank you!

Target Market(s)

Electricity consumers both homes and companies.

Number of Pages Required

1 page

Font styles to use
Serif
Sans Serif

```html
<!DOCTYPE html>
<html lang="en">
<head>
<meta charset="utf-8">
<title>Vindgerdi – Same electricity, just cheaper</title>
<link href="https://fonts.googleapis.com/css2?family=Poppins:wght@400;500;600;700&family=Lato:wght@400;700&display=swap" rel="stylesheet">
<style>
:root{
  --red:#a52a22;
  --red-band:#b5524a;
  --red-soft:#d4918c;
  --navy:#1d3557;
  --ink:#1a1a1a;
  --text:#333;
  --pink:#f8e4e4;
  --grey-card:#ebebed;
  --white:#fff;
  --black:#000;
}
*{margin:0;padding:0;box-sizing:border-box}
html,body{width:1200px;height:3168px;overflow:hidden;background:var(--white)}
body{position:relative;font-family:'Lato',sans-serif;color:var(--text)}
.abs{position:absolute}
h1,h2,h3,h4,.btn,.nav a,.price-value{font-family:'Poppins',sans-serif}

/* header */
.site-header{left:92px;top:0;width:1010px;height:117px;background:var(--white);z-index:3;box-shadow:0 2px 10px rgba(0,0,0,.06)}
.brand{position:absolute;display:flex;align-items:center;gap:10px;font-family:'Poppins',sans-serif;font-weight:600;color:var(--red);text-transform:uppercase}
.brand .dot{width:20px;height:20px;border-radius:50%;background:var(--navy)}
.site-header .brand{left:32px;top:44px;font-size:24px}
.nav{position:absolute;right:20px;top:50px;display:flex;gap:40px}
.nav a{font-size:14.5px;font-weight:600;color:var(--ink);text-decoration:none;text-transform:uppercase}
.nav a.active{color:var(--red)}

/* hero */
.hero-photo{left:0;top:100px;width:1200px;height:520px;background:linear-gradient(180deg,#8c97a3 0%,#b9c0c8 25%,#9aa0a6 45%,#8d7c77 70%,#7b6f6c 100%)}
.hero-band{left:0;top:611px}
.hero-title{left:0;width:1200px;top:375px;text-align:center;font-size:42px;font-weight:700;color:var(--white);text-transform:uppercase}
.hero-sub{left:240px;width:720px;top:441px;text-align:center;font-size:16px;line-height:25px;font-weight:700;color:var(--white);text-transform:uppercase}
.btn{display:flex;align-items:center;justify-content:center;border-radius:5px;font-size:16px;font-weight:500;text-transform:uppercase;text-decoration:none}
.btn-light{background:var(--white);color:var(--red)}
.btn-red{background:var(--red);color:var(--white)}
.hero-btn{left:516px;top:514px;width:145px;height:55px}

/* welcome */
.welcome-photo{left:541px;top:823px;width:545px;height:541px;background:linear-gradient(180deg,#6f9a3f 0%,#5d8a3a 22%,#b9c2c2 45%,#6f8fb0 75%,#3f5f82 100%)}
.welcome-card{left:134px;top:852px;width:499px;height:482px;background:var(--white);box-shadow:0 2px 14px rgba(0,0,0,.1)}
.welcome-card h2{position:absolute;left:27px;top:34px;font-size:33px;font-weight:600;color:var(--ink);text-transform:uppercase}
.welcome-card h3{position:absolute;left:29px;top:92px;width:460px;font-size:20.5px;line-height:24px;font-weight:600;color:var(--ink);text-transform:uppercase}
.welcome-card p{position:absolute;left:29px;top:151px;width:370px;font-size:15px;line-height:24px}
.welcome-card .btn{position:absolute;left:26px;top:385px;width:156px;height:59px}

/* price */
.price-section{left:0;top:1452px;width:1200px;height:676px;background:var(--pink)}
.section-title{width:1200px;left:0;text-align:center;font-size:33px;font-weight:600;color:var(--ink);text-transform:uppercase}
.exchange h3{position:absolute;left:144px;top:1654px;font-size:20.5px;font-weight:600;color:var(--ink);text-transform:uppercase}
.exchange p{position:absolute;left:143px;top:1705px;width:230px;font-family:'Poppins',sans-serif;font-size:15.5px;line-height:24px;color:var(--text)}
.exchange .btn{position:absolute;left:144px;top:1927px;width:147px;height:55px}
.price-card{border-radius:6px;text-align:center}
.price-card.primary{left:462px;top:1601px;width:306px;height:438px;background:var(--white);box-shadow:0 2px 12px rgba(0,0,0,.08);z-index:2}
.price-card.secondary{left:770px;top:1618px;width:279px;height:402px;background:var(--grey-card);box-shadow:0 2px 10px rgba(0,0,0,.08)}
.price-card h4{font-size:19px;font-weight:600;color:var(--ink)}
.price-card .price-value{font-size:37px;font-weight:500;color:var(--ink);line-height:1}
.price-card .unit{font-family:'Poppins',sans-serif;font-size:15px;color:var(--text)}
.price-card .note{font-family:'Poppins',sans-serif;font-size:15.5px;color:var(--text)}
.price-card > *{position:absolute;left:0;width:100%}
.price-card .btn{width:147px;height:55px}

/* future */
.future-photo{left:272px;top:2281px;width:656px;height:322px;background:linear-gradient(90deg,#3d6a8f 0%,#c4b53a 18%,#2f4f6b 35%,#8e6f58 60%,#c97a4a 80%,#6a5a4e 100%)}
.future-text{left:270px;top:2640px;width:660px;text-align:center;font-size:15px;line-height:24px;color:var(--text)}

/* footer */
.site-footer{left:0;top:2775px;width:1200px;height:393px;background:var(--black);color:var(--white)}
.site-footer .brand{left:111px;top:47px;font-size:28px}
.footer-about{left:113px;top:114px;width:290px;font-family:'Poppins',sans-serif;font-size:16px;line-height:26px}
.footer-col h4{font-size:16px;font-weight:600;text-transform:uppercase;margin-bottom:10px}
.footer-col li{list-style:none;font-family:'Poppins',sans-serif;font-size:16px;line-height:26px}
.quick{left:450px;top:42px}
.contact{left:671px;top:42px}
.contact li{display:flex;gap:8px;align-items:flex-start;text-transform:none}
.contact li svg{margin-top:6px;flex:none}
.follow{left:966px;top:42px}
.socials{display:flex;gap:9px}
.socials span{width:34px;height:34px;border-radius:50%;background:var(--red)}
.footer-rule{left:113px;top:278px;width:975px;height:1px;background:#333}
.copyright{left:0;top:313px;width:1200px;text-align:center;font-family:'Poppins',sans-serif;font-size:16px}
</style>
</head>
<body>

<header class="site-header abs">
  <div class="brand"><span class="dot"></span>Vindgerdi</div>
  <nav class="nav">
    <a href="#" class="active">Home</a>
    <a href="#">About Vindgerdi</a>
    <a href="#">Price list</a>
    <a href="#">Future is exciting</a>
    <a href="#">Contact us</a>
  </nav>
</header>

<section class="hero">
  <div class="hero-photo abs" role="img" aria-label="Photo of a snowy Icelandic town with colourful roofs below mountains"></div>
  <svg class="hero-band abs" width="1200" height="140" viewBox="0 0 1200 140">
    <polygon points="0,0 1200,0 1200,139 600,59 0,139" fill="var(--red-soft)"/>
    <polygon points="0,0 1200,0 1200,121 600,31 0,121" fill="var(--red-band)"/>
  </svg>
  <h1 class="hero-title abs">Same electricity just cheaper!</h1>
  <p class="hero-sub abs">Lorem ipsum dolor sit amet consectetur adipiscing elit, sed do eiusmod tempor incididunt ut labore et dolore magna aliqua</p>
  <a class="btn btn-light hero-btn abs" href="#">Learn more</a>
</section>

<section class="welcome">
  <div class="welcome-photo abs" role="img" aria-label="Aerial photo of solar panel rows on green fields"></div>
  <div class="welcome-card abs">
    <h2>Welcome to business</h2>
    <h3>What is Vindgerdi's unique position in the electricity sales market</h3>
    <p>Vindgerdi uses automation and artificial intelligence to achieve lower prices in the electricity market. Our goal is to minimize the cost of energy sales, promote energy balance and offer good service. Vindgerdi's goal is to offer its customers the most favorable electricity prices in Iceland. Electricity is part of the monthly costs of households and companies, and by doing business with Vindgerdi, savings can be achieved and operating costs reduced.</p>
    <a class="btn btn-red" href="#">Learn more</a>
  </div>
</section>

<section class="price-section abs"></section>
<h2 class="section-title abs" style="top:1497px">Vindgerdi price</h2>
<div class="exchange">
  <h3>User exchange</h3>
  <p>If a customer moves and receives a new address during the contract period, this will lead to a change of user. Switching users means that the customer's (user) connection to the electricity system moves from one</p>
  <a class="btn btn-red" href="#">Learn more</a>
</div>
<div class="price-card primary abs">
  <h4 style="top:52px">Make a price comparison</h4>
  <div class="price-value" style="top:102px">6.95</div>
  <div class="unit" style="top:141px">ISK / kWh</div>
  <div class="price-value" style="top:192px">6.22</div>
  <div class="unit" style="top:231px">ISK / kWh</div>
  <div class="note" style="top:272px">electric acceleration</div>
  <a class="btn btn-red" href="#" style="left:77px;top:326px">Order now</a>
</div>
<div class="price-card secondary abs">
  <h4 style="top:35px">Make a price comparison</h4>
  <div class="price-value" style="top:85px">6.95</div>
  <div class="unit" style="top:124px">ISK / kWh</div>
  <div class="price-value" style="top:175px">6.22</div>
  <div class="unit" style="top:214px">ISK / kWh</div>
  <div class="note" style="top:255px">electric acceleration</div>
  <a class="btn btn-red" href="#" style="left:61px;top:309px">Order now</a>
</div>

<section class="future">
  <h2 class="section-title abs" style="top:2207px">The future is exciting</h2>
  <div class="future-photo abs" role="img" aria-label="Photo of a technician inspecting colourful network cables in a workshop"></div>
  <p class="future-text abs">Let's make the electricity system smarter together. Vindgerdi uses artificial intelligence, data science and automation to minimize costs and promote eccentricity</p>
</section>

<footer class="site-footer abs">
  <div class="brand"><span class="dot"></span>Vindgerdi</div>
  <p class="footer-about abs">Lorem ipsum dolor sit amet, consectetur adipiscing elit, sed do eiusmod tempor incididunt ut labore et dolore magna aliqua.</p>
  <div class="footer-col quick abs">
    <h4>Quick link</h4>
    <ul><li>Home</li><li>About vindgerdi</li><li>Price list</li><li>Future is exciting</li><li>Contact us</li></ul>
  </div>
  <div class="footer-col contact abs">
    <h4>Contact</h4>
    <ul>
      <li><svg width="12" height="14" viewBox="0 0 12 16"><path d="M6 0C2.7 0 0 2.6 0 5.9 0 10 6 16 6 16s6-6 6-10.1C12 2.6 9.3 0 6 0zm0 8.2A2.3 2.3 0 1 1 6 3.6a2.3 2.3 0 0 1 0 4.6z" fill="#fff"/></svg><span>LJOSVEGUR 8-10 199<br>VINDHOLT</span></li>
      <li style="margin-top:4px"><svg width="13" height="13" viewBox="0 0 16 16"><path d="M3.5 0.5 6 3.6 4.6 5.6c.9 2.2 3.6 4.9 5.8 5.8l2-1.4 3.1 2.5-1.6 2.9C8.3 15.3.7 7.7.6 2.1z" fill="#fff"/></svg><span>555-0142</span></li>
      <li style="margin-top:4px"><svg width="14" height="11" viewBox="0 0 16 12"><rect x="1" y="1" width="14" height="10" rx="1.5" fill="none" stroke="#fff" stroke-width="1.5"/><path d="M1.5 1.8 8 7l6.5-5.2" fill="none" stroke="#fff" stroke-width="1.5"/></svg><span>vindgerdi@vindgerdi-example.is</span></li>
    </ul>
  </div>
  <div class="footer-col follow abs">
    <h4>Follow us</h4>
    <div class="socials"><span></span><span></span><span></span></div>
  </div>
  <div class="footer-rule abs"></div>
  <p class="copyright abs">© 2021 Vindgerdi All Rights Reserved</p>
</footer>

</body>
</html>
```